Larkspur Talent IT Recruiting firm needs a business card design for Recruiters, Sourcers, and Account

We need business cards that allow us to change all contact info, names, titles (Recruiter, Sourcer, Account Manager, Director, CEO, etc) per person since we have three offices, in three cities, Phoenix, Austin, and Las Vegas. We do recruiting and contractors for IT positions (Developers, Architects, Software Engineers, Security Engineers, Help Desk, DBAs, PMs, Scrum Masters, etc.) Our client companies are very diverse from Meridian 100 to silicone Valley type start-ups.

So, while we what hip, techie, and quirky, it still needs to be professional. Primary color we use is blue, with silver as a secondary color.

Target Market(s)

IT, Technology

Industry/Entity Type

Business

Contact Information for Business Card

Company name: Larkspur Talent, Inc.
Website: www.larkspurtalent.example
Logos for Careerloop, Blipster, and Myriada

Name, Title, Office Number, Cell Number, email

Font styles to use
Serif
Sans Serif

Colors
0455a3
d5d5d5

Requirements
Nice to have
• The grey I selected below is not necessary - but, would like silver included. I included a card design (File 3: LTI early trial example.jpg) that I had started on. It's very rough, and not quite what we're looking for, but what we did like is the logo, big, maybe a bit faded, off center, goes out of frame, etc. Still looking for other ideas - you are the pros! But, just an idea of a design element we liked.

```html
<!DOCTYPE html>
<html lang="en">
<head>
<meta charset="utf-8">
<title>Larkspur Talent — Business Card</title>
<link href="https://fonts.googleapis.com/css2?family=Montserrat:wght@300;400;500;700&display=swap" rel="stylesheet">
<style>
  :root{
    --brand-blue:#0455a3;
    --bright-blue:#1a8fd6;
    --mid-blue:#1f6fc2;
    --ink:#1c1c1e;
    --slate:#4a4f57;
    --paper:#ffffff;
    --paper-shade:#eeeff1;
    --silver:#d5d5d5;
    --backdrop:#e4e6ea;
    --white:#ffffff;
  }
  *{margin:0;padding:0;box-sizing:border-box}
  html,body{width:1200px;height:900px;overflow:hidden}
  body{
    background:var(--backdrop);
    font-family:"Montserrat",sans-serif;
    position:relative;
  }
  .card{
    position:absolute;left:250px;width:700px;height:400px;
    overflow:hidden;
    box-shadow:0 10px 28px rgba(0,0,0,.22);
  }
  /* ---------- back of card ---------- */
  .card--back{
    top:30px;
    background:linear-gradient(160deg,var(--paper) 40%,var(--paper-shade));
  }
  .edge-tab{
    position:absolute;width:30px;height:78px;
    background:linear-gradient(180deg,var(--bright-blue),var(--brand-blue));
  }
  .edge-tab--left{left:0;bottom:80px}
  .edge-tab--right{right:0;top:78px}
  .back-brand{
    position:absolute;top:128px;left:0;right:0;
    display:flex;justify-content:center;align-items:center;gap:14px;
  }
  .back-brand__dot{width:26px;height:26px;border-radius:50%;background:var(--brand-blue)}
  .back-brand__name{
    font-weight:500;font-size:36px;letter-spacing:2px;color:var(--ink);
  }
  .back-tagline{
    position:absolute;top:190px;left:0;right:0;text-align:center;
    font-weight:400;font-size:12px;letter-spacing:4.5px;color:var(--slate);
  }
  .back-web{
    position:absolute;bottom:52px;left:0;right:0;
    display:flex;justify-content:center;align-items:center;gap:8px;
    font-size:11px;letter-spacing:1px;color:var(--slate);
  }
  .back-web svg{width:12px;height:12px}
  /* ---------- front of card ---------- */
  .card--front{
    top:470px;display:flex;
  }
  .front-identity{
    width:46%;height:100%;position:relative;
    background:linear-gradient(160deg,var(--paper) 40%,var(--paper-shade));
  }
  .front-identity__mark{
    position:absolute;left:76px;top:58px;width:170px;height:170px;border-radius:50%;
    background:var(--brand-blue);
  }
  .front-identity__name{
    position:absolute;left:30px;top:250px;
    font-weight:700;font-size:21px;letter-spacing:1px;color:var(--ink);white-space:nowrap;
  }
  .front-identity__tagline{
    position:absolute;left:32px;top:282px;
    font-weight:400;font-size:12px;letter-spacing:3.2px;color:var(--slate);white-space:nowrap;
  }
  .front-contact{
    flex:1;position:relative;color:var(--white);
    background:linear-gradient(160deg,var(--bright-blue),var(--mid-blue) 60%,var(--brand-blue));
  }
  .front-contact__decor{
    position:absolute;right:-60px;top:-40px;width:260px;height:330px;
    border-radius:48% 52% 40% 60%;
    background:radial-gradient(circle at 40% 40%,rgba(255,255,255,.16),rgba(255,255,255,.04) 70%);
  }
  .person{position:absolute;left:30px;top:42px}
  .person__name{font-size:19px;letter-spacing:1px}
  .person__name strong{font-weight:700}
  .person__name span{font-weight:300}
  .person__title{font-weight:300;font-size:11.5px;letter-spacing:1.5px;margin-top:2px}
  .contact-list{position:absolute;left:30px;right:16px;top:108px;list-style:none}
  .contact-list li{
    display:flex;align-items:center;gap:14px;height:32px;
    font-weight:500;font-size:11px;letter-spacing:.8px;white-space:nowrap;
  }
  .contact-icon{
    flex:none;width:22px;height:22px;border:1px solid rgba(255,255,255,.75);border-radius:3px;
    display:flex;align-items:center;justify-content:center;
  }
  .contact-icon svg{width:12px;height:12px}
</style>
</head>
<body>

<section class="card card--back" aria-label="Card back">
  <div class="edge-tab edge-tab--left"></div>
  <div class="edge-tab edge-tab--right"></div>
  <div class="back-brand">
    <div class="back-brand__dot"></div>
    <div class="back-brand__name">LARKSPUR TALENT</div>
  </div>
  <p class="back-tagline">BUILDING TEAMS THAT SHIP</p>
  <p class="back-web">
    <svg viewBox="0 0 12 12"><circle cx="6" cy="6" r="6" fill="#0455a3"/><path d="M1 6h10M6 1c-2 2.5-2 7.5 0 10M6 1c2 2.5 2 7.5 0 10" stroke="#fff" stroke-width=".8" fill="none"/></svg>
    WWW.LARKSPURTALENT.EXAMPLE
  </p>
</section>

<section class="card card--front" aria-label="Card front">
  <div class="front-identity">
    <div class="front-identity__mark"></div>
    <p class="front-identity__name">LARKSPUR TALENT, INC</p>
    <p class="front-identity__tagline">BUILDING TEAMS THAT SHIP</p>
  </div>
  <div class="front-contact">
    <div class="front-contact__decor" role="img" aria-label="Large faded brand symbol running off the card edge"></div>
    <div class="person">
      <p class="person__name"><strong>DANIEL</strong> <span>HART</span></p>
      <p class="person__title">SOFTWARE ENGINEER</p>
    </div>
    <ul class="contact-list">
      <li><span class="contact-icon" aria-label="Myriada"></span>DANIELHART</li>
      <li><span class="contact-icon" aria-label="Blipster"></span>DANIELHART</li>
      <li><span class="contact-icon" aria-label="Careerloop"></span>DANIELHART</li>
      <li><span class="contact-icon" aria-label="Office">
        <svg viewBox="0 0 12 12"><rect x="2" y="2" width="8" height="8" rx="1" fill="none" stroke="#fff" stroke-width="1.2"/></svg>
      </span>555-010-4821</li>
      <li><span class="contact-icon" aria-label="Phone">
        <svg viewBox="0 0 12 12"><path d="M3 1.5l1.6 2.3-1 1.1a6 6 0 0 0 3.5 3.5l1.1-1L10.5 9 9.3 10.5C5 10 2 7 1.5 2.7z" fill="#fff"/></svg>
      </span>555-010-4821</li>
      <li><span class="contact-icon" aria-label="Email">
        <svg viewBox="0 0 12 12"><rect x="1" y="2.5" width="10" height="7" fill="#fff"/><path d="M1 2.5l5 4 5-4" stroke="#1f6fc2" stroke-width="1" fill="none"/></svg>
      </span>DANIELHART@LARKSPURTALENT.EXAMPLE</li>
      <li><span class="contact-icon" aria-label="Website">
        <svg viewBox="0 0 12 12"><circle cx="6" cy="6" r="5.5" fill="#fff"/><path d="M1 6h10M6 1c-2 2.5-2 7.5 0 10M6 1c2 2.5 2 7.5 0 10" stroke="#1f6fc2" stroke-width=".8" fill="none"/></svg>
      </span>WWW.LARKSPURTALENT.EXAMPLE</li>
    </ul>
  </div>
</section>

</body>
</html>
```